Business card design Needed for new logo / Construction business, home extensions and new builds

We need a business card design using our new logo files which i will attach to this project :)

We are a small construction business specialising in home extensions, new builds and property development. We are very ambitious and would appreciate professional and elegant designs for our new business card.

Very serious about using the services on MakerQuarry and recently acquired our new logo from here :)

Please get involved, i will feedback when i can as i am very busy but can respond daily, thanks

Target Market(s)

People that want to build onto their houses, new building developments or adding too their existing property

Industry/Entity Type

Construction

Contact Information for Business Card

Renwick Tolliver Construction, Lionel Ashby (Managing Director), Tel 07822254961, email - info@renwick-tolliver, www.renwick-tolliver.co.uk

Colors

Designer to choose colors to be used in the design.

Requirements
Must have
• I like a deep grey on the back please. A lot of you have provided black from and back, try mixing things up a little. The black looks cool 😎 Thanks

```html
<!DOCTYPE html>
<html lang="en">
<head>
<meta charset="utf-8">
<title>Renwick Tolliver Construction – Business Card</title>
<link rel="stylesheet" href="https://fonts.googleapis.com/css2?family=Montserrat:wght@400;500;700&display=swap">
<style>
  :root {
    --stage: #2a2a2c;
    --back-grey: #3b3b3e;
    --pattern-tone: #47474b;
    --front-black: #141414;
    --gold: #d9a93a;
    --gold-light: #f1c95a;
    --gold-dark: #b07f22;
    --silver: #c9cacc;
    --silver-light: #e6e7e9;
    --white: #f2f2f2;
  }
  * { margin: 0; padding: 0; box-sizing: border-box; }
  html, body {
    width: 1200px; height: 689px; overflow: hidden;
    background: var(--stage);
    font-family: "Montserrat", Arial, sans-serif;
  }
  .canvas {
    width: 1200px; height: 689px;
    display: flex; align-items: center; justify-content: center; gap: 40px;
  }
  .card {
    position: relative;
    width: 540px; height: 309px;
    border-radius: 18px;
    overflow: hidden;
    box-shadow: 0 14px 30px rgba(0,0,0,.45);
  }

  /* Back side */
  .card-back { background: var(--back-grey); }
  .card-back .pattern {
    position: absolute; inset: 0;
    background: linear-gradient(135deg, var(--pattern-tone), var(--back-grey) 60%, #333336);
  }
  .card-back .brand-mark {
    position: absolute; right: 34px; top: 120px;
    display: flex; align-items: center; gap: 8px;
    color: var(--gold); font-weight: 700; font-size: 15px; letter-spacing: .5px;
  }
  .square { width: 14px; height: 14px; background: var(--gold); flex: none; }

  /* Front side */
  .card-front { background: var(--front-black); }
  .brand {
    position: absolute; left: 40px; top: 96px; width: 230px;
    display: flex; flex-direction: column; align-items: center; text-align: center; gap: 12px;
  }
  .brand .square { width: 34px; height: 34px; }
  .brand-name {
    color: var(--gold); font-weight: 700; font-size: 19px;
    letter-spacing: 1.5px; line-height: 1.3; text-transform: uppercase;
  }
  .divider {
    position: absolute; left: 300px; top: 40px;
    width: 1.5px; height: 190px; background: var(--gold);
  }
  .details { position: absolute; left: 322px; top: 44px; }
  .person-name { color: var(--gold); font-weight: 700; font-size: 21px; }
  .person-title { color: var(--white); font-size: 12px; margin-top: 3px; letter-spacing: .3px; }
  .contacts { list-style: none; margin-top: 66px; }
  .contacts li {
    display: flex; align-items: center; gap: 8px;
    color: var(--white); font-size: 11.5px; margin-bottom: 7px;
  }
  .contacts svg { width: 12px; height: 12px; flex: none; }
  .bands { position: absolute; left: 0; bottom: 0; width: 540px; height: 70px; }
</style>
</head>
<body>
<main class="canvas">

  <section class="card card-back" aria-label="Card back">
    <div class="pattern" role="img" aria-label="Tonal embossed repeating monogram pattern on deep grey"></div>
    <div class="brand-mark"><span class="square"></span>Renwick Tolliver</div>
  </section>

  <section class="card card-front" aria-label="Card front">
    <div class="brand">
      <span class="square"></span>
      <p class="brand-name">Renwick Tolliver<br>Construction</p>
    </div>

    <div class="divider"></div>

    <div class="details">
      <h1 class="person-name">Lionel Ashby</h1>
      <p class="person-title">Managing Director</p>
      <ul class="contacts">
        <li>
          <svg viewBox="0 0 12 12" aria-hidden="true"><path fill="var(--gold)" d="M1 4c0-1.5 2-2.5 5-2.5S11 2.5 11 4v1H8.5V3.8C7.7 3.6 4.3 3.6 3.5 3.8V5H1zM3 6h6l1.5 4.5h-9z"/></svg>
          07822254961
        </li>
        <li>
          <svg viewBox="0 0 12 12" aria-hidden="true"><rect x="1" y="2.5" width="10" height="7" fill="var(--gold)"/><path d="M1 2.5l5 4 5-4" stroke="var(--front-black)" fill="none"/></svg>
          info@renwick-tolliver
        </li>
        <li>
          <svg viewBox="0 0 12 12" aria-hidden="true"><circle cx="6" cy="6" r="5" fill="var(--gold)"/><path d="M1 6h10M6 1c-2.5 2.5-2.5 7.5 0 10M6 1c2.5 2.5 2.5 7.5 0 10" stroke="var(--front-black)" stroke-width=".8" fill="none"/></svg>
          www.renwick-tolliver.co.uk
        </li>
      </ul>
    </div>

    <svg class="bands" viewBox="0 0 540 70" aria-hidden="true">
      <defs>
        <linearGradient id="goldBand" x1="0" x2="1">
          <stop offset="0" stop-color="var(--gold-dark)"/>
          <stop offset=".5" stop-color="var(--gold-light)"/>
          <stop offset="1" stop-color="var(--gold)"/>
        </linearGradient>
        <linearGradient id="silverBand" x1="0" x2="1">
          <stop offset="0" stop-color="var(--silver)"/>
          <stop offset=".6" stop-color="var(--silver-light)"/>
          <stop offset="1" stop-color="var(--silver)"/>
        </linearGradient>
      </defs>
      <polygon points="0,58 318,58 330,44 336,44 336,70 0,70" fill="url(#silverBand)"/>
      <polygon points="340,22 540,22 540,70 322,70" fill="url(#goldBand)"/>
    </svg>
  </section>

</main>
</body>
</html>
```